Kelvara Pools

Luxury pool designer builder brochure

Company name is "Kelvara"
Tag line is "Pools for the Mind Body & Soul"
Maybe integrate "Luxury Urban Lifestyle"

Target Market(s)

30 to 65 income of 200000.00 plus Affluent, high end life style
Luxury living

Industry/Entity Type

It Company

Font styles to use
Serif

Colors
000000

Requirements
Must have
• NOTE:
• Please remove the "Aquatic environments for the under the logo.
• I want a black background with a very contemporary feel.
• This is a luxury lifestyle product.

```html
<!DOCTYPE html>
<html lang="en">
<head>
<meta charset="utf-8">
<title>Kelvara Pools — Brochure Cover</title>
<link href="https://fonts.googleapis.com/css2?family=Bodoni+Moda:opsz,wght@6..96,400&display=swap" rel="stylesheet">
<style>
  :root {
    --ink: #000000;
    --paper: #ffffff;
    --fold: #6e6e6e;
  }
  html, body {
    margin: 0;
    padding: 0;
    width: 1200px;
    height: 849px;
    overflow: hidden;
    background: var(--ink);
  }
  .spread {
    position: relative;
    width: 1200px;
    height: 849px;
    background: var(--ink);
    color: var(--paper);
    font-family: "Bodoni Moda", "Times New Roman", serif;
  }
  .fold-line {
    position: absolute;
    left: 600px;
    top: 0;
    width: 1px;
    height: 849px;
    background: var(--fold);
  }
  .back-address {
    position: absolute;
    left: 0;
    width: 600px;
    top: 778px;
    text-align: center;
    font-size: 16px;
    letter-spacing: 0.3px;
  }
  .cover-tagline {
    position: absolute;
    right: 42px;
    top: 334px;
    margin: 0;
    text-align: right;
    font-weight: 400;
    font-size: 38px;
    line-height: 43px;
    letter-spacing: 0.6px;
  }
  .cover-brand {
    position: absolute;
    right: 42px;
    top: 775px;
    font-size: 19px;
    letter-spacing: 1px;
  }
</style>
</head>
<body>
  <main class="spread">
    <section class="back-cover">
      <p class="back-address">address</p>
    </section>
    <div class="fold-line"></div>
    <section class="front-cover">
      <h1 class="cover-tagline">Pools for the Mind<br>Body &amp; Soul</h1>
      <div class="cover-brand">Kelvara</div>
    </section>
  </main>
</body>
</html>
```